Tender / Request for Quotation response template

KELVARA42 is a small consulting company that works in management consulting with a particular emphasis on tourism, sport, major events and general commercial. our clients range from government , councils, private businesses and industry associations.

we are regularly asked to submit detailed quotes or tender responses and we use our own PowerPoint template to do so as we find it its generally easier to work with.

our website provides more detail : www.kelvara42.com.au the colour of the blue in logo is #000033

our submissions range from 30 pages to 100 pages depending on the size and scale of the project - so we need flexibility with the templates.

Our submissions generally include cover page and table of contents and then
1. Project overview
2. About KELVARA42
3. The project team including bios
4. Initial Insights
5. importance of sustainability
6. Project methodology - example being
6.1 situation analysis
- research
- consultation and engagement
- relevant audits
- relevant economic analysis including graphs
- gap analysis
- SWOT
6.2 Issues and opportunities
6.3 draft report
6.4 final report
7. Case studies and previous relevant work
8. Project timeline
9. Project budget
10. Insurance and referees

we use many graphs and tables from excel and images generally sourced from the web. we also use icons as appropriate so we need graph templates - column, bar / pie etc and table templates.

the feel is on the formal corporate side given the size and scale of projects and clients but with bright and clear graphics and photos.

i have attached 2 copies of confidential submissions that we have made in recent weeks. one long form and one short form to give you an idea of the flexibility we need in the submission process.

if we are happy with the proposed PowerPoint tender submission template we would then look to have a similar one created to use in the development of the actual reports themselves .

hopefully this provides enough information but if not please reach out for more information

our logo and general format are in the attached examples

Target Market(s)

government, council, corporates and private businesses

Industry/Entity Type

management consulting with emphasis on tourism sport major events nd general commerical

Other font styles liked:
• we usually use calbiri but open to other standard microsoft off the shelf fonts

Colors
0054AA
0677BA
7BADD7
CADEEF
E8F1F8
0094D4
00A9DD
6FCCEA
C7EBF8
E9F6FB

Requirements
Must have
• page for each of the sections detailed in the project brief. image placement - small and large, table and graph formats,

```html
<!DOCTYPE html>
<html lang="en">
<head>
<meta charset="utf-8">
<title>KELVARA42 – Tender Response Template</title>
<link href="https://fonts.googleapis.com/css2?family=Exo+2:wght@500;600;700&family=Raleway:wght@400;500;600;700&display=swap" rel="stylesheet">
<style>
  :root{
    --navy:#000033;
    --blue:#0054AA;
    --blue-mid:#0677BA;
    --sky:#7BADD7;
    --ice:#E8F1F8;
    --page-bg:#f3f3f5;
    --ink:#222230;
    --body:#3a3a44;
    --pie-red:#C0504D;
    --pie-blue:#4F81BD;
    --pie-green:#9BBB59;
    --pie-grey:#A5A5A5;
  }
  *{box-sizing:border-box;margin:0;padding:0}
  html,body{width:1200px;height:1162px;overflow:hidden;background:var(--page-bg)}
  body{position:relative;font-family:"Raleway",sans-serif;color:var(--body);font-variant-numeric:lining-nums;font-feature-settings:"lnum" 1}

  .slide{position:absolute;width:542px;height:305px;background:linear-gradient(135deg,#ffffff 0%,#f7f8fa 60%,#fbfbfc 100%);box-shadow:0 2px 6px rgba(0,0,40,.12);overflow:hidden}
  .col-left{left:42px}
  .col-right{left:620px}
  .row-1{top:64px}
  .row-2{top:420px}
  .row-3{top:769px}

  .section-band{position:absolute;left:0;top:23px;height:37px;background:var(--blue);border-radius:0 19px 19px 0;color:#fff;font-family:"Exo 2",sans-serif;font-weight:600;font-size:12.3px;line-height:37px;padding-left:29px;white-space:nowrap}
  .brand-dot{position:absolute;top:23px;right:16px;width:25px;height:25px;border:1.6px solid var(--navy);border-radius:50%}
  .page-no{position:absolute;left:494px;top:280px;height:18px;border-left:2.5px solid var(--blue);padding-left:8px;font-size:10px;line-height:18px;color:var(--ink);font-weight:500}

  /* cover */
  .cover-visual{position:absolute;inset:0}
  .cover-name{position:absolute;left:0;width:262px;top:186px;text-align:center;font-family:"Exo 2",sans-serif;font-weight:600;font-size:29px;color:var(--navy);letter-spacing:.5px}
  .cover-ring{position:absolute;left:87px;top:89px;width:90px;height:90px;border:4px solid var(--navy);border-radius:50%}

  /* contents */
  .toc{position:absolute;top:76px;list-style:none;font-size:9.8px;line-height:15.5px;color:var(--ink)}
  .toc-a{left:46px}
  .toc-b{left:302px}

  .copy{position:absolute;text-align:justify;hyphens:auto;color:var(--body)}
  .overview-copy{left:29px;top:78px;width:486px;font-size:6.9px;line-height:11.3px}
  .about-copy{left:28px;top:79px;width:244px;font-size:7.3px;line-height:11.2px}
  .about-copy p+p{margin-top:2.5px}
  .method-copy{left:29px;top:78px;width:236px;font-size:7.3px;line-height:10.7px}
  .method-copy p+p{margin-top:10.7px}
  .case-copy{left:28px;top:74px;width:295px;font-size:7.3px;line-height:11.3px}

  .photo{position:absolute;left:298px;top:66px;width:212px;height:112px;background:linear-gradient(160deg,#dfe6ef 0%,#b9c3cf 45%,#6f6a63 75%,#8e8478 100%)}
  .badge{position:absolute;width:52px;height:18px;border-radius:3px}

  .wheel{position:absolute;left:277px;top:53px;width:230px;height:230px}
  .wheel text{font-family:"Exo 2",sans-serif;font-weight:500;font-size:8px;fill:#fff}

  .chart-box{position:absolute;left:335px;width:158px;border:1px solid #555;background:#fff}
  .chart-box h4{font-family:"Raleway",sans-serif;font-weight:700;font-size:4.8px;line-height:6px;text-align:center;color:#222;padding:4px 14px 0}
  .chart-box .src{font-size:2.8px;text-align:center;color:#777;line-height:4px}
  .chart-box svg{display:block;margin:0 auto}
  .chart-box svg text{font-family:"Raleway",sans-serif;font-size:5px;fill:#333}
</style>
</head>
<body>

<!-- Cover -->
<section class="slide col-left row-1 cover">
  <svg class="cover-visual" viewBox="0 0 542 305">
    <defs>
      <clipPath id="coverClip">
        <path d="M402 0 A150 150 0 0 0 402 300 L542 305 L542 0 Z"/>
      </clipPath>
      <linearGradient id="coverTone" x1="0" y1="0" x2="1" y2="1">
        <stop offset="0" stop-color="#f4f0f4"/>
        <stop offset=".35" stop-color="#f2a39c"/>
        <stop offset=".55" stop-color="#c9c6dc"/>
        <stop offset=".8" stop-color="#8f9fc4"/>
        <stop offset="1" stop-color="#e7ecf5"/>
      </linearGradient>
    </defs>
    <rect role="img" aria-label="Photo collage of business people silhouettes over a city skyline" x="250" y="0" width="292" height="305" fill="url(#coverTone)" clip-path="url(#coverClip)"/>
    <path d="M402 0 A150 150 0 0 0 402 300" fill="none" stroke="var(--navy)" stroke-width="2.6"/>
  </svg>
  <div class="cover-ring"></div>
  <div class="cover-name">KELVARA42</div>
</section>

<!-- Table of contents -->
<section class="slide col-right row-1">
  <div class="section-band" style="width:217px">Table Of Contents</div>
  <div class="brand-dot"></div>
  <ul class="toc toc-a">
    <li>1. Project overview</li>
    <li>2. About KELVARA42</li>
    <li>3. The project team includes bios</li>
    <li>4. Initial Insights</li>
    <li>5. importance of sustainability</li>
    <li>6. Project methodology - example being</li>
    <li>6.1 situation analysis</li>
    <li>- research</li>
    <li>- consultation and engagement</li>
    <li>- relevant audits</li>
    <li>- relevant economic analysis including graphs</li>
    <li>- gap analysis</li>
    <li>- SWOT</li>
  </ul>
  <ul class="toc toc-b">
    <li>6.2 Issues and opportunities</li>
    <li>6.3 draft report</li>
    <li>6.4 final report</li>
    <li>7. Case studies and previous relevant work</li>
    <li>8. Project timeline</li>
    <li>9. Project budget</li>
    <li>10. Insurance and referees</li>
  </ul>
  <div class="page-no">Page 2</div>
</section>

<!-- Project overview -->
<section class="slide col-left row-2">
  <div class="section-band" style="width:218px">Project Overview</div>
  <div class="brand-dot"></div>
  <div class="copy overview-copy">
    <p>Having been established in 2020, the Southern Shoreline Coast &amp; Parks Authority (SSCPA) has the principle purpose of protecting, conserving, enhancing and managing Crown land and coastal assets within the Southern Shoreline coast and parks area.</p>
    <p>SSCPA was also set up by the State Government as a self sustaining entity – meaning that it must meet its operating and maintenance costs from its own revenue streams. This is not without challenges for SSCPA. At present, the largest source of revenue for SSCPA is the caravan parks and campgrounds that it currently operates. KELVARA42 has the pleasure of currently working with SSCPA on developing the strategic plan for those caravan parks and campgrounds. One of that Plan's purpose is to ensure that they not only provide the required revenue to manage the parks, but also provide additional funds to enable the Authority to meet its other core conservation and sustainability obligations. That Plan is close to completion and there are a number of synergies to this project.</p>
    <p>Another potential source of revenue for SSCPA is the revenue optimisation of the vast amounts of Crown land that fall within its remit. This does not mean that SSCPA can simply run commercial enterprises and activities across all its land. Any activation and optimisation strategy must be conducive with SSCPA's overarching ambit of protecting, conserving and enhancing the region. It must also do it in away that builds social licence and is supported by the Traditional Owners. Where possible, leadership of any activities should be undertaken with those Traditional Owners.</p>
    <p>This project will involve researching, understanding, and identifying opportunities for the appropriate utilisation of Crown land reserves (under the remit of SSCPA). There are a number of options and opportunities that will be considered through this strategy. The key requirement though is to ensure that the Traditional Owners as rightsholders, other key stakeholders and the local community all have the opportunity to input into the development of those concepts. This is extremely important to ensure that social licence is built for those activities and are consistent with the general views of the community across the region.</p>
  </div>
  <div class="page-no">Page 3</div>
</section>

<!-- About -->
<section class="slide col-right row-2">
  <div class="section-band" style="width:217px">About KELVARA42</div>
  <div class="brand-dot"></div>
  <div class="copy about-copy">
    <p>Our founder, Daniel Ashby, saw a real need for a new style of business advisory and executive support service for Small and Medium sized Enterprises (SME) and Government businesses. Particularly in the sectors in which he had worked for over 20 years – sport, tourism, major events and "for purpose". They often had resource issues or complex matters that needed addressing but, for a number of reasons, could not be serviced adequately by the top tier consulting companies.</p>
    <p>Daniel set out to address the issue and KELVARA42 was born.</p>
    <p>He has built a network of consultants and specialists who are experts in their relevant disciplines. In KELVARA42 the team work together to deliver first class meaningful, relevant and affordable consulting and advisory services.</p>
    <p>We understand the short and long term opportunities and issues facing our clients and we work closely with them across the whole 360 degrees of their business operations. We bring a new and fresh approach to business advisory services and support</p>
  </div>
  <div class="photo" role="img" aria-label="Photo of two hikers helping each other climb a rocky summit under a cloudy sky"></div>
  <div class="badge" style="left:306px;top:200px;background:#1f4f8f"></div>
  <div class="badge" style="left:376px;top:200px;background:#2a2a44"></div>
  <div class="badge" style="left:447px;top:200px;background:#d9672a"></div>
  <div class="badge" style="left:306px;top:240px;background:#b9ae6e"></div>
  <div class="badge" style="left:376px;top:240px;background:#4aa33d"></div>
  <div class="badge" style="left:447px;top:240px;background:#c4123a"></div>
  <div class="page-no">Page 4</div>
</section>

<!-- Methodology -->
<section class="slide col-left row-3">
  <div class="section-band" style="width:271px">Project methodology - Example Being</div>
  <div class="brand-dot"></div>
  <div class="copy method-copy">
    <p>To ensure a clear understanding of the current situation facing HTA in regards to its Fashion Collection, as well as identification of issues and opportunities that might help inform the future approach to the Costume Collection, a situation analysis will be undertaken.</p>
    <p>This will include an initial desk top review of HTA documentation and other related aspects that will help to identify existing solutions for other collections managed by the HTA across Australia as well as other international examples that are seen as exemplars for the management of historical collections.</p>
    <p>A mapping process to identify existing and potential supporters of the Costume Collection and HTA more broadly will be undertaken. This will hopefully identify opportunities for closer partnerships into the future. Alongside this we will look wider afield and identify other partners that have close affiliation with the fashion industry in the region, and Australia wide, that could be potential supporters into the future.</p>
  </div>
  <svg class="wheel" viewBox="-115 -115 230 230" aria-label="Methodology cycle">
    <circle r="110" fill="var(--navy)" stroke="var(--blue)" stroke-width="3"/>
    <g stroke="#c8d2e6" stroke-width=".8">
      <line x1="0" y1="-33" x2="0" y2="-109"/>
      <line x1="31.4" y1="-10.2" x2="103.7" y2="-33.7"/>
      <line x1="19.4" y1="26.7" x2="64.1" y2="88.2"/>
      <line x1="-19.4" y1="26.7" x2="-64.1" y2="88.2"/>
      <line x1="-31.4" y1="-10.2" x2="-103.7" y2="-33.7"/>
    </g>
    <circle r="33" fill="#fff"/>
    <text x="-56" y="-55"><tspan x="-56">Final</tspan><tspan x="-56" dy="10">Reports</tspan></text>
    <text x="18" y="-56"><tspan x="18">Situation</tspan><tspan x="18" dy="10">Analysis</tspan></text>
    <text x="50" y="8"><tspan x="50">Market</tspan><tspan x="50" dy="10">Research</tspan></text>
    <text x="-20" y="75"><tspan x="-20">Issues &amp;</tspan><tspan x="-20" dy="10">Opportunities</tspan></text>
    <text x="-89" y="7"><tspan x="-89">Financial</tspan><tspan x="-89" dy="10">Analysis</tspan></text>
  </svg>
  <div class="page-no">Page 5</div>
</section>

<!-- Case studies -->
<section class="slide col-right row-3">
  <div class="section-band" style="width:299px">Case Studies And Previous Relevant Work</div>
  <div class="brand-dot"></div>
  <div class="copy case-copy">
    <p>As one way of providing a guide to potential visitors to a HTA Fashion facility we profiled the domestic visitors to Marlowe who visited an art gallery or museum on their visit. To focus more intensively on fashion-oriented visitors, we focused data analysis to only the second quarter of the year in 2016 and 2021 to 2022 the period in which three of the six Marlowe Art Gallery fashion exhibitions in recent years were held.</p>
    <p>In these three quarters domestic overnight visitors to East Marlowe who visited an art gallery or museum were a total of 169,000 or more than double this class of domestic visitors in the second quarter of 2017-2019 (79,000) when no fashion exhibits were held.</p>
    <p>In the three June quarters in years 2016, 2021 and 2022 of total overnight visitors to East Marlowe, 27% had the activity of visiting an art gallery or museum – a very high market share.</p>
    <p>Women provided more than 75% of domestic overnight visitors to East Marlowe (who visited an art gallery or museum during their stay) in the June quarters of 2016, 2021 and 2022. In contrast, in 2017-19 June quarters the share of women in these visitors was only 54%. Over 55s provided 61% of domestic overnight visitors (15+ in age) to East Marlowe who visited an art gallery or museum during their stay in 2016, 2021 and 2022. In contrast, in 2017-19 the share of 55+ in these visitors was lower at 53%.</p>
  </div>

  <div class="chart-box" style="top:56px;height:103px">
    <h4>Women dominated in overnight visitors to East Marlowe with activity of visiting art galleries and museums in 2016, 2021 and 2022</h4>
    <div class="src">Source: NTR Regional Traveller Study</div>
    <svg width="150" height="76" viewBox="-75 -38 150 76">
      <circle r="35" fill="var(--pie-red)"/>
      <path d="M0 0 L0 -35 A35 35 0 0 1 34.93 -2.2 Z" fill="var(--pie-blue)"/>
      <text x="36" y="-25">Male</text><text x="38" y="-18">24%</text>
      <text x="-56" y="8">Female</text><text x="-51" y="15">76%</text>
    </svg>
  </div>

  <div class="chart-box" style="top:168px;height:104px">
    <h4>Over 55s dominated in overnight visitors to East Marlowe with activity of visiting art galleries and museums in 2016, 2021 and 2022</h4>
    <div class="src">Source: NTR Regional Traveller Study</div>
    <svg width="150" height="76" viewBox="-75 -36 150 76">
      <circle r="35" fill="var(--pie-grey)"/>
      <path d="M0 0 L0 -35 A35 35 0 0 1 22.3 27 Z" fill="var(--pie-green)"/>
      <text x="44" y="5">Under 54</text><text x="50" y="12">39%</text>
      <text x="-60" y="8">55+</text><text x="-61" y="15">61%</text>
    </svg>
  </div>
  <div class="page-no">Page 6</div>
</section>

</body>
</html>
```